Business card design Needed for new logo / Construction business, home extensions and new builds

We need a business card design using our new logo files which i will attach to this project :)

We are a small construction business specialising in home extensions, new builds and property development. We are very ambitious and would appreciate professional and elegant designs for our new business card.

Very serious about using the services on MakerQuarry and recently acquired our new logo from here :)

Please get involved, i will feedback when i can as i am very busy but can respond daily, thanks

Target Market(s)

People that want to build onto their houses, new building developments or adding too their existing property

Industry/Entity Type

Construction

Contact Information for Business Card

Renwick Tolliver Construction, Lionel Ashby (Managing Director), Tel 07822254961, email - info@renwick-tolliver, www.renwick-tolliver.co.uk

Colors

Designer to choose colors to be used in the design.

Requirements
Must have
• I like a deep grey on the back please. A lot of you have provided black from and back, try mixing things up a little. The black looks cool 😎 Thanks

```html
<!DOCTYPE html>
<html lang="en">
<head>
<meta charset="utf-8">
<title>Renwick Tolliver Construction – Business Card</title>
<link rel="stylesheet" href="https://fonts.googleapis.com/css2?family=Cinzel:wght@600&family=Open+Sans:wght@400;600;700&display=swap">
<style>
  :root {
    --page: #151518;
    --card: #1e1e23;
    --card-back: #26262b;
    --gold: #e0a825;
    --gold-soft: #c99a3a;
    --silver: #d9dade;
    --white: #f4f4f4;
    --emboss: #18181c;
  }
  * { box-sizing: border-box; margin: 0; padding: 0; }
  html, body {
    width: 1200px; height: 780px; overflow: hidden;
    background: var(--page);
  }
  .canvas {
    width: 1200px; height: 780px;
    display: flex; align-items: center; justify-content: center; gap: 40px;
  }
  .card {
    width: 560px; height: 320px;
    border-radius: 22px;
    border: 2px solid var(--gold);
    position: relative; overflow: hidden;
  }
  .card-back { background: var(--card-back); }
  .card-front { background: var(--card); }

  /* Back */
  .back-name {
    position: absolute; inset: 0;
    display: flex; flex-direction: column; align-items: center; justify-content: center; gap: 6px;
    font-family: "Cinzel", serif; font-weight: 600; color: var(--emboss);
    text-align: center;
  }
  .back-mark { width: 44px; height: 44px; background: var(--emboss); margin-bottom: 10px; }
  .back-name .line-1 { font-size: 34px; letter-spacing: 1px; }
  .back-name .line-2 { font-size: 20px; letter-spacing: 3px; }

  /* Front */
  .company {
    position: absolute; left: 40px; top: 58px;
    display: flex; align-items: center; gap: 12px;
    font-family: "Cinzel", serif; font-weight: 600; color: var(--silver);
  }
  .company-mark { width: 30px; height: 30px; background: var(--gold); flex: none; }
  .company-name { font-size: 17px; line-height: 1.25; letter-spacing: .5px; }

  .person {
    position: absolute; right: 58px; top: 44px; text-align: right;
    font-family: "Open Sans", sans-serif;
  }
  .person-name { font-size: 30px; font-weight: 700; color: var(--white); line-height: 1.1; }
  .person-name .surname { color: var(--gold); }
  .person-role { font-size: 14px; color: var(--white); margin-top: 2px; }
  .gold-bar {
    position: absolute; right: 36px; top: 40px;
    width: 10px; height: 62px; background: linear-gradient(180deg, var(--gold), var(--gold-soft));
  }

  .address {
    position: absolute; left: 40px; top: 140px;
    font-family: "Open Sans", sans-serif; font-size: 16px; line-height: 1.45; color: var(--white);
  }
  .contacts {
    position: absolute; left: 40px; bottom: 30px; list-style: none;
    font-family: "Open Sans", sans-serif; font-size: 15px; color: var(--white);
  }
  .contacts li { display: flex; align-items: center; gap: 10px; line-height: 1.6; }
  .contacts svg { width: 14px; height: 14px; fill: var(--gold); flex: none; }
</style>
</head>
<body>
<main class="canvas">

  <section class="card card-back" aria-label="Card back">
    <div class="back-name">
      <div class="back-mark"></div>
      <span class="line-1">Renwick Tolliver</span>
      <span class="line-2">Construction</span>
    </div>
  </section>

  <section class="card card-front" aria-label="Card front">
    <div class="company">
      <div class="company-mark"></div>
      <div class="company-name">Renwick Tolliver<br>Construction</div>
    </div>

    <div class="person">
      <p class="person-name">Lionel <span class="surname">Ashby</span></p>
      <p class="person-role">Managing Director</p>
    </div>
    <div class="gold-bar"></div>

    <address class="address">
      Harrow Lane, Elmbridge<br>
      Westcombe, WC4 7RT
    </address>

    <ul class="contacts">
      <li>
        <svg viewBox="0 0 24 24" aria-hidden="true"><path d="M6.6 10.8a15.1 15.1 0 0 0 6.6 6.6l2.2-2.2a1 1 0 0 1 1-.25 11.4 11.4 0 0 0 3.6.57 1 1 0 0 1 1 1V20a1 1 0 0 1-1 1A17 17 0 0 1 3 4a1 1 0 0 1 1-1h3.5a1 1 0 0 1 1 1c0 1.25.2 2.45.57 3.57a1 1 0 0 1-.25 1z"/></svg>
        0782 225 4961
      </li>
      <li>
        <svg viewBox="0 0 24 24" aria-hidden="true"><path d="M2 5h20v14H2zm2 2v.5l8 5 8-5V7zm0 2.8V17h16V9.8l-8 5z"/></svg>
        info@renwick-tolliver.co.uk
      </li>
      <li>
        <svg viewBox="0 0 24 24" aria-hidden="true"><path d="M12 2a10 10 0 1 0 0 20 10 10 0 0 0 0-20zm6.9 9h-3a15 15 0 0 0-1.4-6A8 8 0 0 1 18.9 11zM12 4c.9 1.2 1.8 3.6 2 7h-4c.2-3.4 1.1-5.8 2-7zM9.5 5a15 15 0 0 0-1.4 6h-3A8 8 0 0 1 9.5 5zM5.1 13h3a15 15 0 0 0 1.4 6A8 8 0 0 1 5.1 13zM12 20c-.9-1.2-1.8-3.6-2-7h4c-.2 3.4-1.1 5.8-2 7zm2.5-1a15 15 0 0 0 1.4-6h3a8 8 0 0 1-4.4 6z"/></svg>
        www.renwick-tolliver.co.uk
      </li>
    </ul>
  </section>

</main>
</body>
</html>
```